Physiotherapy Referral Pad

-Need a referral pad for physiotherapy to be provided to doctors' offices. I would like it to be simple, not too cluttered and sharp looking so doctors can quickly complete it for clients.

-I have attached my logo which I would like to include. I have also included my business cards to keep the style, font, colors etc consistent.

-I would like to include my slogan
From Our Home To Yours

-I would like it to include services options with tick boxes for Mobile, Clinic, Telehealth, NRPDLA

-I would like for it to say Call to Book or Book Online

-I would like it to include my clinic address:
472 Marrow Crescent
Whitehorse, YT
Y2B3K9

-I would like it to include my contact info:
Glen Ostrow BSc(kin), MPT, CAFCI, IMS
(867)555-0142
physio@ostrowtherapy.ca

-I would like lines for the following:
Patient Name:
Diagnosis/Recommendations:
(extra lines to fill out patient info)

Physician Signature
Date

Target Market(s)

Physicians to refer clients to physiotherapy

Industry/Entity Type

Physical Therapy

Requirements
Must have
• Clean, concise, easy to look at and find pertinant categories for physicians
Nice to have
• Ostrow Therapy color scheme. Please see business cards and website as needed
Should not have
• Not too cluttered or wordy

```html
<!DOCTYPE html>
<html lang="en">
<head>
<meta charset="utf-8">
<title>Ostrow Therapy – Physiotherapy Referral Pad</title>
<link rel="stylesheet" href="https://fonts.googleapis.com/css2?family=Cormorant+SC:wght@600;700&family=Roboto:wght@400&display=swap">
<style>
  :root {
    --forest: #12563a;
    --royal: #233a8f;
    --ink: #444444;
    --rule: #6b6b6b;
    --paper: #ffffff;
    --backdrop: #e6e7e9;
    --tint: #e9ebf4;
  }
  * { margin: 0; padding: 0; box-sizing: border-box; }
  html, body { width: 1200px; height: 1200px; overflow: hidden; background: var(--backdrop); }
  .pad {
    position: absolute; left: 242px; top: 94px; width: 714px; height: 1010px;
    background: var(--paper); font-family: "Cormorant SC", Georgia, serif;
  }
  .center { position: absolute; left: 0; width: 100%; text-align: center; }
  .brand-mark { position: absolute; left: 332px; top: 80px; width: 50px; height: 50px; background: var(--royal); }
  .brand-name { top: 148px; font-size: 48px; font-weight: 700; letter-spacing: 4px; color: var(--forest); line-height: 1; }
  .therapist { top: 236px; font-size: 41px; font-weight: 700; color: var(--forest); line-height: 1; letter-spacing: 1px; }
  .credentials { top: 278px; font-size: 18px; font-weight: 700; color: var(--royal); }
  .booking { top: 320px; font-size: 25px; font-weight: 700; color: var(--forest); letter-spacing: 1.5px; }
  .address { top: 352px; font-family: "Roboto", Arial, sans-serif; font-size: 19px; color: var(--ink); }
  .contacts { top: 375px; font-family: "Roboto", Arial, sans-serif; font-size: 19px; color: var(--ink);
    display: flex; justify-content: center; align-items: center; gap: 8px; }
  .contacts svg { width: 18px; height: 18px; flex: none; }
  .contacts span { margin-right: 4px; }
  .services { top: 418px; display: flex; justify-content: center; gap: 10px;
    font-size: 21px; font-weight: 700; color: var(--royal); letter-spacing: 1px; }
  .services label { display: flex; align-items: center; gap: 8px; }
  .services i { width: 17px; height: 17px; border: 2px solid var(--forest); display: inline-block; }
  .decor { position: absolute; left: 170px; top: 690px; width: 370px; height: 310px; background: var(--tint); opacity: .8; }
  .label { position: absolute; font-size: 20px; font-weight: 700; color: var(--royal); letter-spacing: 1px; line-height: 1; }
  .line { position: absolute; height: 0; border-top: 1.5px solid var(--rule); }
  .slogan-band { position: absolute; left: 0; top: 957px; width: 714px; height: 36px; }
  .slogan { position: absolute; left: 0; width: 100%; top: 964px; text-align: center;
    font-size: 19px; font-weight: 700; color: #fff; letter-spacing: 2.5px; }
</style>
</head>
<body>
<main class="pad">
  <div class="brand-mark"></div>
  <div class="center brand-name">OSTROW THERAPY</div>
  <h1 class="center therapist">GLEN OSTROW</h1>
  <p class="center credentials">BSc(kin), MPT, CAFCI, IMS</p>
  <p class="center booking">Call to Book or Book Online</p>
  <p class="center address">472 Marrow Crescent Whitehorse, YT Y2B3K9</p>
  <p class="center contacts">
    <svg viewBox="0 0 20 20"><circle cx="10" cy="10" r="10" fill="#12563a"/><path d="M6.5 5.5l2 .2.8 2.2-1.2 1a6 6 0 003 3l1-1.2 2.2.8.2 2c-4 .8-8.8-4-8-8z" fill="#fff"/></svg>
    <span>(867)555-0142</span>
    <svg viewBox="0 0 20 20"><circle cx="10" cy="10" r="10" fill="#12563a"/><rect x="5" y="6.5" width="10" height="7" fill="#fff"/><path d="M5 6.5l5 4 5-4" stroke="#12563a" fill="none"/></svg>
    <span>physio@ostrowtherapy.ca</span>
    <svg viewBox="0 0 20 20"><circle cx="10" cy="10" r="10" fill="#12563a"/><circle cx="10" cy="10" r="5" fill="none" stroke="#fff" stroke-width="1.6"/><path d="M5 10h10M10 5v10" stroke="#fff" stroke-width="1.2"/></svg>
    <span>www.ostrowtherapy.ca</span>
  </p>
  <div class="center services">
    <label><i></i>MOBILE</label>
    <label><i></i>CLINIC</label>
    <label><i></i>TELEHEALTH</label>
    <label><i></i>NRPDLA</label>
  </div>

  <div class="decor" aria-hidden="true"></div>

  <span class="label" style="left:74px;top:514px">PATIENT NAME:</span>
  <div class="line" style="left:256px;top:533px;width:382px"></div>
  <div class="line" style="left:74px;top:594px;width:564px"></div>

  <span class="label" style="left:74px;top:630px">Diagnosis/Recommendations:</span>
  <div class="line" style="left:408px;top:651px;width:230px"></div>
  <div class="line" style="left:74px;top:711px;width:564px"></div>
  <div class="line" style="left:77px;top:770px;width:564px"></div>

  <span class="label" style="left:77px;top:810px">Physician Signature</span>
  <div class="line" style="left:316px;top:831px;width:324px"></div>

  <span class="label" style="left:77px;top:870px">Date</span>
  <div class="line" style="left:138px;top:891px;width:502px"></div>

  <svg class="slogan-band" viewBox="0 0 714 36" preserveAspectRatio="none" aria-hidden="true">
    <rect x="0" y="0" width="714" height="29" fill="#12563a"/>
    <polygon points="94,0 620,0 596,29 118,29" fill="#233a8f"/>
    <polygon points="72,0 94,29 50,29" fill="#ffffff"/>
    <polygon points="642,0 664,29 620,29" fill="#ffffff"/>
  </svg>
  <p class="slogan">FROM OUR HOME TO YOURS</p>
</main>
</body>
</html>
```